The Brandwell Firm

We need a new design for our letterhead and envelopes. We are a personal injury and criminal defense firm so we need something modern and clean, but more on the professional/traditional side. Our new logo has two colors and is attached to the file so we need something that works well with those colors/matches the design. The following information needs to be on the letterhead:
Phone: (555) 214-3370
Fax: (555) 214-5186
Toll-Free: (888) 431-2059
Post Office Box 4721
Millbrook, SC 29555-4721
HarmClaimCounsel.example
PalmettoTrialAdvocates.example

Target Market(s)

Clients, government agencies, other law firms

Industry/Entity Type

Legal

Font styles to use
Sans Serif
Other font styles liked:
• Arial

Colors

Designer to choose colors to be used in the design.

Requirements
Must have
• Must look professional and clean, modern
Nice to have
• I would like to see a design that works with the logo but does not distract from the content that will be printed on it
Should not have
• Too many colors or crazy designs.

```html
<!DOCTYPE html>
<html lang="en">
<head>
<meta charset="utf-8">
<title>The Brandwell Firm – Letterhead</title>
<link href="https://fonts.googleapis.com/css2?family=Open+Sans:wght@400;600&display=swap" rel="stylesheet">
<style>
  :root {
    --backdrop: #e9e9ea;
    --paper: #ffffff;
    --brand-red: #d31f26;
    --brand-navy: #2b3990;
    --ink-grey: #4a4a4a;
    --band-text: #ffffff;
  }
  * { margin: 0; padding: 0; box-sizing: border-box; }
  html, body {
    width: 1200px; height: 1200px; overflow: hidden;
    background: var(--backdrop);
    font-family: "Open Sans", Arial, sans-serif;
  }
  .letterhead {
    position: absolute;
    left: 207px; top: 40px;
    width: 786px; height: 1120px;
    background: var(--paper);
    box-shadow: 0 2px 10px rgba(0,0,0,0.12);
  }
  .brand {
    position: absolute;
    left: 50px; top: 118px;
    display: flex; align-items: center; gap: 10px;
  }
  .brand-dot {
    width: 14px; height: 14px; border-radius: 50%;
    background: var(--brand-red);
  }
  .brand-name {
    font-weight: 600; font-size: 26px; letter-spacing: 0.2px;
    color: var(--brand-navy);
  }
  .header-web {
    position: absolute;
    right: 54px; top: 142px;
    font-size: 13.5px;
  }
  .header-web .domain { color: var(--brand-red); }
  .header-web .tld { color: var(--ink-grey); }
  .footer-band {
    position: absolute;
    left: 0; bottom: 0;
    width: 100%; height: 45px;
    background: var(--brand-red);
    color: var(--band-text);
    font-size: 12px;
    text-align: center;
    padding-top: 4px;
    line-height: 19px;
  }
  .contact-row {
    display: flex; justify-content: center; gap: 10px;
  }
  .contact-item { display: inline-flex; align-items: center; gap: 5px; }
  .contact-item svg { width: 10px; height: 10px; fill: var(--band-text); }
</style>
</head>
<body>
  <main class="letterhead">
    <div class="brand">
      <span class="brand-dot"></span>
      <span class="brand-name">The Brandwell Firm</span>
    </div>
    <div class="header-web"><span class="domain">HarmClaimCounsel</span><span class="tld">.example</span></div>

    <footer class="footer-band">
      <div class="address">Post Office Box 4721 Millbrook, SC 29555-4721</div>
      <div class="contact-row">
        <span class="contact-item">
          <svg viewBox="0 0 10 10"><path d="M2 0.5 L3.6 2.6 L2.8 3.6 Q3.8 5.8 6.4 7.2 L7.4 6.4 L9.5 8 L8.2 9.5 Q2.5 8.5 0.5 1.8 Z"/></svg>
          (555) 214-3370
        </span>
        <span class="contact-item">
          <svg viewBox="0 0 10 10"><rect x="2.5" y="0.5" width="5" height="3"/><rect x="0.5" y="3.5" width="9" height="4" rx="1"/><rect x="2.5" y="6" width="5" height="3.5"/></svg>
          (555) 214-5186
        </span>
        <span class="contact-item">
          <svg viewBox="0 0 10 10"><path d="M2 0.5 L3.6 2.6 L2.8 3.6 Q3.8 5.8 6.4 7.2 L7.4 6.4 L9.5 8 L8.2 9.5 Q2.5 8.5 0.5 1.8 Z"/></svg>
          (888) 431-2059 (Toll-Free)
        </span>
        <span class="contact-item">
          <svg viewBox="0 0 10 10"><circle cx="5" cy="5" r="4.3" fill="none" stroke="#fff" stroke-width="0.9"/><ellipse cx="5" cy="5" rx="1.8" ry="4.3" fill="none" stroke="#fff" stroke-width="0.8"/><line x1="0.7" y1="5" x2="9.3" y2="5" stroke="#fff" stroke-width="0.8"/></svg>
          PalmettoTrialAdvocates.example
        </span>
      </div>
    </footer>
  </main>
</body>
</html>
```